Professional Single Page Website Design for Tollbrook Advisory

Tollbrook Advisory is a new business consultancy specializing in providing expert services to small businesses, primarily in the brick-and-mortar retail and food service sectors. We offer a range of services including franchise development and launch, due diligence, and construction management.

Currently, we have a basic website set up at www.tollbrookadvisory.example, but we need a professional touch to enhance its design and functionality.

Project Requirements:
- Single Page Design: For now, we need a single page design that effectively showcases who we are, our services, and contact information.
- Future Expansion: The design should be flexible and scalable for future expansion to include additional pages like specific service offerings, about us, and a dedicated contact page.
- Design Aesthetic: We are looking for a modern yet professional design that aligns with our brand identity.
- Logo: We have a logo that we like, which was also sourced from Pixel Bazaar. The logo files are attached to this project brief.

Key Sections to Include:
- Hero Section: An engaging introduction to Tollbrook Advisory with a strong visual impact.
- About Us: A brief overview of who we are and our mission.
- Team: Section for the profiles of the two principals.
- Services: A clear and concise presentation of our services, including franchise development, due diligence, and construction management.
- Contact Information: Easy-to-find contact details, including a form for inquiries.
- Call to Action: Encouraging visitors to get in touch with us for consultations or further information.

Design Considerations:
- Ensure the design is responsive and mobile-friendly.
- Include high-quality images and icons that complement our services and industry.
- We do not need development services, this is only a design project.

```html
<!DOCTYPE html>
<html lang="en">
<head>
<meta charset="utf-8">
<title>Tollbrook Advisory</title>
<link href="https://fonts.googleapis.com/css2?family=Poppins:wght@400;500;600;700;800&display=swap" rel="stylesheet">
<style>
:root{
  --navy:#1f2a33;
  --navy-deep:#1b252d;
  --mint:#93c9b0;
  --mint-dark:#7dbb9f;
  --ink:#23282d;
  --body:#5a5f63;
  --white:#ffffff;
  --soft:#f4f6f6;
}
*{box-sizing:border-box;margin:0;padding:0}
html,body{width:1200px;height:3506px;overflow:hidden}
body{font-family:'Poppins',sans-serif;color:var(--ink);background:var(--white);position:relative}

/* nav */
.topbar{position:absolute;left:0;top:0;width:1200px;height:60px;background:var(--navy);z-index:3}
.nav-link{position:absolute;top:21px;color:var(--white);font-size:13px;font-weight:600;letter-spacing:.2px}
.social{position:absolute;top:14px;width:33px;height:33px;border-radius:50%;background:var(--white)}
.brand-tab{position:absolute;left:497px;top:0;width:206px;height:190px;background:var(--mint);z-index:4;
  clip-path:polygon(0 0,100% 0,100% 160px,50% 190px,0 160px);display:flex;flex-direction:column;align-items:center;padding-top:24px}
.brand-dot{width:60px;height:60px;border-radius:50%;background:var(--navy)}
.brand-name{margin-top:14px;font-size:15px;font-weight:500;color:var(--navy)}

/* hero */
.hero{position:absolute;left:0;top:60px;width:1200px;height:600px;
  background:linear-gradient(180deg,#2a3433 0%,#3b3a2f 35%,#4a3c28 55%,#2b3524 80%,#1e2a22 100%)}
.hero-shade{position:absolute;inset:0;background:rgba(15,20,22,.35)}
.hero-kicker{position:absolute;left:0;width:1200px;top:256px;text-align:center;color:var(--mint);font-size:23px;font-weight:600}
.hero-title{position:absolute;left:0;width:1200px;top:295px;text-align:center;color:var(--white);font-size:63px;font-weight:800;line-height:82px}
.btn{position:absolute;height:41px;border-radius:21px;font-size:13px;font-weight:600;display:flex;align-items:center;justify-content:center}
.btn-mint{background:var(--mint);color:var(--navy)}
.btn-white{background:var(--white);color:var(--navy)}
.scroll-bump{position:absolute;left:545px;top:624px;width:110px;height:36px;background:var(--white);border-radius:55px 55px 0 0}
.scroll-icon{position:absolute;left:589px;top:643px;width:22px;height:32px;border-radius:11px;background:var(--navy)}

/* about */
.about{position:absolute;left:0;top:703px;width:1200px;height:644px;
  background:linear-gradient(180deg,#f5f7f7 0%,#eef1f2 60%,#ffffff 100%)}
.about-visual{position:absolute;left:84px;top:97px;width:479px;height:479px;border-radius:40px;
  background:linear-gradient(135deg,#a8d6c1 0%,#3d7e64 45%,#1f5a45 100%)}
.h2{font-size:43px;font-weight:800;line-height:60px;color:var(--ink)}
.h2 .accent{color:var(--mint)}
.about-title{position:absolute;left:622px;top:100px;width:520px}
.about-text{position:absolute;left:622px;top:234px;width:470px;font-size:14px;line-height:37px;color:var(--body)}
.btn-square{position:absolute;left:622px;top:522px;width:114px;height:41px;border-radius:4px;background:var(--mint-dark);color:var(--navy);
  font-size:13px;font-weight:600;display:flex;align-items:center;justify-content:center}

/* services */
.serve-title{position:absolute;left:0;width:1200px;top:1385px;text-align:center}
.serve-intro{position:absolute;left:0;width:1200px;top:1460px;text-align:center;font-size:13.5px;line-height:33px;color:var(--body)}
.card{position:absolute;top:1559px;width:320px;height:414px;background:var(--white);box-shadow:0 6px 24px rgba(0,0,0,.08)}
.card-media{width:320px;height:231px}
.card-title{margin-top:34px;text-align:center;font-size:16px;font-weight:700;color:var(--ink)}
.card-text{margin:10px 28px 0;text-align:center;font-size:12.5px;line-height:27px;color:var(--body)}
.arrow{position:absolute;width:20px;height:20px;border-radius:50%}

/* team */
.team-mint{position:absolute;left:0;top:2079px;width:757px;height:554px;background:var(--mint)}
.team-navy{position:absolute;left:757px;top:2079px;width:443px;height:554px;background:var(--navy)}
.team-title{position:absolute;left:111px;top:2172px;font-size:43px;font-weight:800;color:var(--navy)}
.team-role{position:absolute;left:111px;top:2248px;font-size:20px;font-weight:700;color:var(--navy)}
.team-bio{position:absolute;left:111px;top:2290px;width:485px;font-size:13.5px;line-height:30px;color:var(--navy)}
.btn-navy{position:absolute;left:111px;top:2492px;width:136px;height:37px;border-radius:19px;background:var(--navy);color:var(--mint);
  font-size:13px;font-weight:600;display:flex;align-items:center;justify-content:center}
.team-photo{position:absolute;left:671px;top:2150px;width:416px;height:415px;background:linear-gradient(180deg,#b9cfe0 0%,#c9d3cf 45%,#e7e9ea 100%)}

/* contact */
.contact{position:absolute;left:0;top:2633px;width:1200px;height:557px;
  background:linear-gradient(180deg,#ffffff 0%,#ffffff 62%,#c9cfd6 82%,#8e98a3 100%)}
.contact-title{position:absolute;left:0;width:1200px;top:2722px;text-align:center}
.info-icon{position:absolute;left:130px;width:40px;height:40px;border-radius:50%;background:var(--mint);display:flex;align-items:center;justify-content:center}
.info-label{position:absolute;left:186px;font-size:13px;font-weight:600;color:var(--ink)}
.info-value{position:absolute;left:186px;font-size:13px;line-height:26px;color:var(--body)}
.field{position:absolute;left:458px;width:290px;height:45px;background:var(--white);box-shadow:0 3px 14px rgba(0,0,0,.08);
  font-size:11px;color:#777;padding:15px 26px}
.field-msg{position:absolute;left:780px;top:2830px;width:290px;height:240px;background:var(--white);box-shadow:0 3px 14px rgba(0,0,0,.08);
  font-size:11px;color:#777;padding:15px 26px}
.send{position:absolute;left:458px;top:3026px;width:290px;height:44px;background:var(--mint-dark);color:var(--navy);
  font-size:13px;font-weight:600;display:flex;align-items:center;justify-content:center}

/* footer */
.footer{position:absolute;left:0;top:3190px;width:1200px;height:316px;background:var(--navy)}
.foot-mark{position:absolute;left:160px;top:70px;width:122px;height:122px;border-radius:50%;background:var(--mint)}
.foot-brand{position:absolute;left:111px;top:208px;font-size:25px;font-weight:500;color:var(--white)}
.foot-col{position:absolute;top:70px}
.foot-col h4{font-size:19px;font-weight:700;color:var(--white);margin-bottom:14px}
.foot-col a{display:block;font-size:14px;color:var(--white);line-height:32px;text-decoration:none}
.copyright{position:absolute;left:0;width:1200px;top:276px;text-align:center;font-size:13.5px;color:var(--white)}
</style>
</head>
<body>

<section class="hero" role="img" aria-label="Evening photograph of a house among trees with warm lit windows">
  <div class="hero-shade"></div>
</section>

<header class="topbar">
  <span class="nav-link" style="left:113px">HOME</span>
  <span class="nav-link" style="left:231px">ABOUT US</span>
  <span class="nav-link" style="left:376px">SERVICES</span>
  <span class="nav-link" style="left:752px">TEAM</span>
  <span class="nav-link" style="left:867px">CONTACT US</span>
  <span class="social" style="left:1010px"></span>
  <span class="social" style="left:1054px"></span>
</header>
<div class="brand-tab">
  <div class="brand-dot"></div>
  <div class="brand-name">Tollbrook Advisory</div>
</div>

<p class="hero-kicker">EXPERTISE AT EVERY STEP: FROM PLANNING TO EXECUTION</p>
<h1 class="hero-title">BUILDING SUCCESS IN<br>SOUTHERN CALIFORNIA</h1>
<a class="btn btn-mint" style="left:442px;top:482px;width:150px">GET STARTED</a>
<a class="btn btn-white" style="left:607px;top:482px;width:150px">CONTACT US</a>
<div class="scroll-bump"></div>
<div class="scroll-icon">
  <svg width="22" height="32" viewBox="0 0 22 32"><path d="M11 8v15M6 18l5 5 5-5" stroke="#fff" stroke-width="1.8" fill="none" stroke-linecap="round"/></svg>
</div>

<section class="about">
  <div class="about-visual" role="img" aria-label="Tall glass office towers seen from below, tinted green"></div>
  <h2 class="h2 about-title">ABOUT <span class="accent">TOLLBROOK ADVISORY</span></h2>
  <p class="about-text">Welcome to Tollbrook Advisory, your trusted partner in navigating the complexities of the real estate and small business markets. Founded by industry veterans Daniel Okafor and Ravi Lindqvist, we specialize in providing comprehensive services tailored to the unique needs of our clients. Whether you're a franchisee, a new restaurant owner, or a commercial real estate investor, Our expertise in due diligence, construction management</p>
  <a class="btn-square">Read More</a>
</section>

<h2 class="h2 serve-title">WHAT <span class="accent">WE SERVE</span></h2>
<p class="serve-intro">At Tollbrook, we blend innovative strategies with local market expertise to guide your commercial real estate ventures.<br>Whether you're launching a new restaurant, investing in retail spaces, or expanding a franchise</p>

<span class="arrow" style="left:43px;top:1756px;background:#cfd3d6"><svg width="20" height="20" viewBox="0 0 20 20"><path d="M11.5 6 7.5 10l4 4" stroke="#fff" stroke-width="2" fill="none"/></svg></span>
<span class="arrow" style="left:1136px;top:1756px;background:var(--navy)"><svg width="20" height="20" viewBox="0 0 20 20"><path d="M8.5 6l4 4-4 4" stroke="#fff" stroke-width="2" fill="none"/></svg></span>

<article class="card" style="left:94px">
  <div class="card-media" role="img" aria-label="Hand touching a glowing network of storefront icons" style="background:radial-gradient(circle at 50% 45%,#c7794a 0%,#3a3f52 45%,#1b2230 100%)"></div>
  <h3 class="card-title">FRANCHISE DEVELOPMENT</h3>
  <p class="card-text">Comprehensive franchise setup from evaluation to launch for scalable business growth.</p>
</article>
<article class="card" style="left:441px">
  <div class="card-media" role="img" aria-label="Hands reviewing charts on a tablet and paper reports" style="background:linear-gradient(135deg,#d9dde2 0%,#8a96a6 50%,#2c333c 100%)"></div>
  <h3 class="card-title">DUE DILIGENCE</h3>
  <p class="card-text">Conducting thorough due diligence for business and property transactions to identify potential risks and liabilities.</p>
</article>
<article class="card" style="left:786px">
  <div class="card-media" role="img" aria-label="Engineers in safety vests studying building plans" style="background:linear-gradient(135deg,#4a4d50 0%,#6b6b66 50%,#2b2d2f 100%)"></div>
  <h3 class="card-title">CONSTRUCTION MANAGEMENT</h3>
  <p class="card-text">Our Building &amp; Construction Management Services oversee every aspect of your construction</p>
</article>

<div class="team-mint"></div>
<div class="team-navy"></div>
<h2 class="team-title">OUR LEADERSHIP TEAM</h2>
<h3 class="team-role">DANIEL OKAFOR (PRINCIPAL)</h3>
<p class="team-bio">Daniel Okafor brings almost 20 years of rich experience as a real estate investor and a pivotal role at one of southern California's largest real estate management firms, where he led sales and marketing strategies to elevate property value and investor returns. His vast expertise spans through strategic development and market analysis, making him a cornerstone for Tollbrook Advisory.</p>
<a class="btn-navy">View Details</a>
<div class="team-photo" role="img" aria-label="Portrait of the principal on a rooftop overlooking a city"></div>
<span class="arrow" style="left:1130px;top:2330px;background:var(--white)"><svg width="20" height="20" viewBox="0 0 20 20"><path d="M8.5 6l4 4-4 4" stroke="#1f2a33" stroke-width="2" fill="none"/></svg></span>
<span class="arrow" style="left:1130px;top:2362px;border:1.5px solid #4a5560"><svg width="17" height="17" viewBox="0 0 20 20"><path d="M11.5 6 7.5 10l4 4" stroke="#4a5560" stroke-width="2" fill="none"/></svg></span>

<section class="contact" role="img" aria-label="Faded city skyline along the bottom of the contact section"></section>
<h2 class="h2 contact-title">GET IN TOUCH <span class="accent">WITH US</span></h2>

<span class="info-icon" style="top:2838px"><svg width="14" height="16" viewBox="0 0 14 16"><path d="M7 1a5 5 0 0 0-5 5c0 4 5 9 5 9s5-5 5-9a5 5 0 0 0-5-5zm0 7a2 2 0 1 1 0-4 2 2 0 0 1 0 4z" fill="#1f2a33"/></svg></span>
<span class="info-label" style="top:2834px">Location:</span>
<span class="info-value" style="top:2855px;width:240px">412 Meridian Way Suite 200, Lakeport,<br>CA 90210, USA</span>
<span class="info-icon" style="top:2946px"><svg width="14" height="14" viewBox="0 0 14 14"><path d="M3 1l2 3-1.3 1.3a8 8 0 0 0 5 5L10 9l3 2-1 2c-6 0-11-5-11-11z" fill="#1f2a33"/></svg></span>
<span class="info-label" style="top:2941px">Contact Number:</span>
<span class="info-value" style="top:2962px">+1 555 010 4477 (Call)</span>
<span class="info-icon" style="top:3021px"><svg width="14" height="12" viewBox="0 0 14 12"><rect x="1" y="1" width="12" height="10" rx="1" fill="#1f2a33"/><path d="M1.5 2l5.5 4 5.5-4" stroke="#93c9b0" stroke-width="1.2" fill="none"/></svg></span>
<span class="info-label" style="top:3016px">Email Address:</span>
<span class="info-value" style="top:3037px">info@tollbrookadvisory.example</span>

<div class="field" style="top:2830px">Full Name</div>
<div class="field" style="top:2895px">Email Address</div>
<div class="field" style="top:2959px">Contact Number</div>
<a class="send">Send Message</a>
<div class="field-msg">Message</div>

<footer class="footer">
  <div class="foot-mark"></div>
  <div class="foot-brand">Tollbrook Advisory</div>
  <div class="foot-col" style="left:415px"><h4>QUICK LINKS</h4><a>Individuals</a><a>Teams</a><a>Agencies</a><a>Features</a></div>
  <div class="foot-col" style="left:615px"><h4>SUPPORT</h4><a>Pricing</a><a>Integrations</a><a>About Us</a></div>
  <div class="foot-col" style="left:787px"><h4>HELP LINKS</h4><a>Help</a><a>Support</a><a>Privacy Policy</a><a>Terms Of Use</a></div>
  <div class="foot-col" style="left:975px"><h4>FOLLOW US</h4><a>Chirpline</a><a>Snapwell</a><a>Linkpost</a></div>
  <p class="copyright">(C) Copyright 2024 | All Rights Reserved</p>
</footer>

</body>
</html>
```